Church Offering Envelope for receive weekly offerings

I need the front of an 6 3/4 envelope designed to be a church offering envelope. Our color palette is CMYK, 1a56b7, e8da7e, 19a3a3, 40c7f1, e7282d.
I need all of the text information carried forward from our old envelope (see attached) but the new style needs to be modern and flat. (Don't want another dove and clouds theme) I need a 1/4 border on all four sides as envelopes cannot be printed full bleed.
Logo is attached
Target Market(s)
Church
Industry/Entity Type
Church
Font styles to use
Sans Serif
Requirements
Must have
- must adhere to the color palette is CMYK, 1a56b7, e8da7e, 19a3a3, 40c7f1, e7282d.
- I need all of the text information carried forward from our old envelope (see attached)

```html
<!DOCTYPE html>
<html lang="en">
<head>
<meta charset="utf-8">
<title>Grace Harbor Ministries – Offering Envelope</title>
<link rel="stylesheet" href="https://fonts.googleapis.com/css2?family=Source+Sans+3:wght@400;600&display=swap">
<style>
  :root {
    --royal-blue: #1a56b7;
    --wheat: #e8da7e;
    --teal: #19a3a3;
    --sky: #40c7f1;
    --red: #e7282d;
    --paper: #ffffff;
    --panel: #faf6e3;
    --ink: #1f2a3c;
    --rule: #5a6474;
  }
  * { box-sizing: border-box; margin: 0; padding: 0; }
  html, body { width: 1200px; height: 638px; overflow: hidden; background: var(--paper); }
  body { font-family: "Source Sans 3", Arial, sans-serif; color: var(--ink); }

  .envelope { position: relative; width: 1200px; height: 638px; background: var(--paper); }

  /* quarter-inch unprinted margin on all four sides */
  .print-area {
    position: absolute;
    left: 46px; top: 46px;
    width: 1108px; height: 546px;
    background: var(--panel);
    overflow: hidden;
  }

  .verse-panel {
    position: absolute;
    left: 714px; top: 0;
    width: 394px; height: 546px;
    background: var(--royal-blue);
  }
  .dove-area {
    position: absolute;
    left: 60px; top: 210px;
    width: 300px; height: 300px;
    border-radius: 50%;
    background: var(--sky);
  }
  .top-stripe {
    position: absolute;
    left: 0; top: 0;
    width: 714px; height: 10px;
    background: var(--wheat);
  }
  .bottom-stripe {
    position: absolute;
    left: 0; bottom: 0;
    width: 714px; height: 10px;
    background: var(--teal);
  }

  .ministry-name {
    position: absolute;
    left: 34px; top: 86px;
    font-size: 40px;
    font-weight: 600;
    color: var(--royal-blue);
    white-space: nowrap;
  }
  .name-accent {
    position: absolute;
    left: 36px; top: 146px;
    width: 90px; height: 4px;
    background: var(--red);
  }

  .verse {
    position: absolute;
    left: 14px; top: 40px;
    width: 366px;
    text-align: center;
    font-size: 20px;
    line-height: 31px;
    color: var(--paper);
  }
  .verse cite { font-style: normal; font-weight: 600; }

  .field-row {
    position: absolute;
    display: flex;
    align-items: baseline;
    font-size: 22px;
    white-space: nowrap;
  }
  .field-line {
    display: inline-block;
    border-bottom: 1.5px dashed var(--rule);
    height: 1px;
  }
  .check-box {
    display: inline-block;
    width: 18px; height: 18px;
    border: 1.5px solid var(--ink);
    margin-right: 7px;
    transform: translateY(2px);
  }
  .name-field { left: 34px; top: 336px; }
  .name-field .field-line { width: 570px; margin-left: 8px; }
  .tithe-field { left: 34px; top: 416px; }
  .tithe-field .field-line { width: 140px; margin-left: 10px; }
  .media-field { left: 380px; top: 416px; }
  .media-field .field-line { width: 130px; margin-left: 10px; }

  .funds-note {
    position: absolute;
    left: 20px; top: 494px;
    width: 674px;
    text-align: center;
    font-size: 15px;
  }
</style>
</head>
<body>
  <main class="envelope">
    <section class="print-area">
      <div class="top-stripe"></div>
      <div class="bottom-stripe"></div>

      <aside class="verse-panel">
        <div class="dove-area" role="img" aria-label="Dove in flight"></div>
        <blockquote class="verse">
          <p>“Honour the LORD with thy substance,<br>and with the firstfruits<br>of all thine increase:”;</p>
          <cite>Prov 3:9</cite>
        </blockquote>
      </aside>

      <h1 class="ministry-name">Grace Harbor Ministries</h1>
      <div class="name-accent"></div>

      <div class="field-row name-field">Name:<span class="field-line"></span></div>
      <div class="field-row tithe-field"><span class="check-box"></span>Tithe/Offering<span class="field-line"></span></div>
      <div class="field-row media-field"><span class="check-box"></span>Radio/Webcast<span class="field-line"></span></div>

      <p class="funds-note">Grace Harbor Ministries does not receive restricted funds in amounts less than $10,000</p>
    </section>
  </main>
</body>
</html>
```